Laser Tattoo Removal Business Cards

We are looking for a professional business card design for a laser tattoo removal business. Ideally looking for a black business card design. The name of the business is Brightline Tattoo Removal. We place our cards at local tattoo shops so we ideally are looking for something trendy/edgy to draw both male and female clientele in.

Target Market(s)

Male/Female ages 18-60

Contact Information for Business Card

black background ideally.. hoping to stay within greys, whites and black

Font styles to use
Serif
Sans Serif

Colors
121212
a9a9a9
5c5c5c
f5f5f5
ffffff
7f7f7f
606060
848484
9d9d9d

Requirements
Must have
• Employee Info:
• Melissa Thornbury
• Chief Executive Offer
• m: 919.537.2846
• w: 919.362.4178
• f: 919.685.3907
• mthornbury@brightlinetattooremoval.example
• Address:
• 4615 Oakmere Pkwy, Suite 210
• Raleigh, NC 27654
• Website:
• www.brightlinetattooremoval.example
Nice to have
• Myabe business name on back or logo on back and employee info on the front

```html
<!DOCTYPE html>
<html lang="en">
<head>
<meta charset="utf-8">
<title>Brightline Tattoo Removal – Business Cards</title>
<link rel="stylesheet" href="https://fonts.googleapis.com/css2?family=Roboto:wght@400&family=Roboto+Condensed:wght@400;700&display=swap">
<style>
  :root {
    --ink-black: #121212;
    --card-dark: #1f1f1f;
    --stage: #2b2b2b;
    --paper: #f5f5f5;
    --paper-shade: #dcdcdc;
    --white: #ffffff;
    --grey-light: #a9a9a9;
    --grey-mid: #7f7f7f;
    --grey-dark: #5c5c5c;
    --rule: #9d9d9d;
  }
  * { margin: 0; padding: 0; box-sizing: border-box; }
  html, body {
    width: 1200px;
    height: 960px;
    overflow: hidden;
    background: var(--stage);
  }
  .canvas {
    position: relative;
    width: 1200px;
    height: 960px;
  }
  .card {
    position: absolute;
    left: 322px;
    width: 600px;
    height: 342px;
  }
  .card-front { top: 108px; }
  .card-back {
    top: 494px;
    background: var(--card-dark);
    display: flex;
    align-items: center;
    justify-content: center;
  }
  .front-texture {
    position: absolute;
    inset: 0;
    background: radial-gradient(ellipse at 45% 40%, var(--paper) 0%, #e8e8e8 60%, var(--paper-shade) 100%);
  }
  .employee {
    position: absolute;
    right: 346px;
    top: 152px;
    text-align: right;
  }
  .employee-name {
    font-family: "Roboto Condensed", sans-serif;
    font-weight: 700;
    font-size: 21px;
    line-height: 22px;
    color: #2a2a2a;
    text-transform: uppercase;
    white-space: nowrap;
  }
  .employee-title {
    font-family: "Roboto", sans-serif;
    font-size: 14px;
    line-height: 18px;
    color: var(--grey-light);
    white-space: nowrap;
  }
  .divider {
    position: absolute;
    left: 275px;
    top: 112px;
    width: 1px;
    height: 130px;
    background: var(--rule);
    opacity: 0.6;
  }
  .contact {
    position: absolute;
    left: 299px;
    top: 100px;
    font-family: "Roboto", sans-serif;
    font-size: 14px;
    line-height: 19px;
    color: var(--grey-dark);
    white-space: nowrap;
  }
  .contact-address { margin-bottom: 8px; }
  .brand-name {
    font-family: "Roboto Condensed", sans-serif;
    font-weight: 700;
    font-size: 30px;
    letter-spacing: 3px;
    color: var(--white);
    text-transform: uppercase;
    text-align: center;
    line-height: 40px;
  }
</style>
</head>
<body>
<main class="canvas">
  <section class="card card-front">
    <div class="front-texture" role="img" aria-label="Light grey damask pattern covering the card face"></div>
    <div class="employee">
      <p class="employee-name">Melissa Thornbury</p>
      <p class="employee-title">Chief Executive Offer</p>
    </div>
    <div class="divider"></div>
    <div class="contact">
      <div class="contact-address">
        <p>4615 Oakmere Pkwy, Suite 210</p>
        <p>Raleigh, NC 27654</p>
      </div>
      <p>(P) 919.362.4178</p>
      <p>(M) 919.537.2846</p>
      <p>(F) 919.685.3907</p>
      <p>mthornbury@brightlinetattooremoval.example</p>
      <p>www.brightlinetattooremoval.example</p>
    </div>
  </section>

  <section class="card card-back">
    <p class="brand-name">Brightline<br>Tattoo Removal</p>
  </section>
</main>
</body>
</html>
```